Business Card Design

Carl Brenton Insurance Agency, an Independent Insurance Agency which was stated on Pine Street in Laplace, Louisiana on 1958 and has grown the six locations throughout South Louisiana. We sell personal (auto Homeowners flood, liability) and commercial insurance (commercial property, general liability, workers compensation, commercial auto). I am looking for a double sided card with list the five remaining locations on the back or maybe even a folded four sided card. Our home office is a two story building with a green roof. I have had a logo designed which I have attached. Open for revisions but would like to stay with in the same green roof over an M. I have attached the logo but can not tell if I was uploaded.

Target Market(s)

Individual and commercial insurance buyers. Upper income and business owners

Industry/Entity Type

Insurance

Requirements
Must have
• Must have similar logo as uploaded. Green roof over M or something similar. List all location address and phone numbers.

Employee name, office phone number; direct phone line; email address and website list all locations on card. Very Similar colors to current logo.
Nice to have
• Possible folded card with double sided print

```html
<!DOCTYPE html>
<html lang="en">
<head>
<meta charset="utf-8">
<title>Carl Brenton Insurance Agency – Business Card</title>
<link rel="stylesheet" href="https://fonts.googleapis.com/css2?family=Cinzel:wght@400&family=Roboto:wght@400;700&display=swap">
<style>
  :root {
    --bg: #e9e7e3;
    --paper: #ffffff;
    --green: #1f6b45;
    --blue: #1682c8;
    --slate: #6f8879;
    --ink: #222222;
    --muted: #7a7f7c;
  }
  html, body {
    margin: 0;
    width: 1200px;
    height: 858px;
    overflow: hidden;
    background: var(--bg);
  }
  .canvas { position: relative; width: 1200px; height: 858px; }

  .card {
    position: absolute;
    width: 600px;
    height: 343px;
    background: var(--paper);
    box-shadow: 0 6px 18px rgba(0,0,0,.18);
    overflow: hidden;
    font-family: "Roboto", Arial, sans-serif;
  }
  .card--front { left: 70px; top: 70px; }
  .card--back  { left: 530px; top: 445px; }

  .brand { position: absolute; display: flex; align-items: center; gap: 12px; }
  .brand__square { width: 26px; height: 26px; background: var(--green); flex: none; }
  .brand__name {
    color: var(--green);
    font-weight: 700;
    font-size: 23px;
    line-height: 1.05;
    letter-spacing: .5px;
    text-transform: uppercase;
  }
  .tagline { position: absolute; color: var(--muted); font-weight: 700; font-size: 13px; white-space: nowrap; }

  .card--front .brand { left: 40px; top: 46px; }
  .card--front .tagline { left: 78px; top: 106px; }

  .employee {
    position: absolute;
    left: 200px; top: 180px;
    font-family: "Cinzel", Georgia, serif;
    font-size: 19px;
    color: var(--ink);
    letter-spacing: 1px;
    white-space: nowrap;
  }

  .band { position: absolute; bottom: 0; color: #fff; font-size: 15px; line-height: 1.45; }
  .band--phones { left: 0; width: 288px; height: 78px; background: var(--blue); padding: 14px 0 0 120px; box-sizing: border-box; }
  .band--web { right: 0; width: 300px; height: 104px; background: var(--slate); padding: 40px 0 0 70px; box-sizing: border-box; }
  .band__row { display: flex; align-items: center; gap: 8px; white-space: nowrap; }
  .band__row svg { width: 13px; height: 13px; flex: none; }

  .card--back .brand { left: 170px; top: 30px; }
  .card--back .tagline { left: 208px; top: 88px; }

  .locations {
    position: absolute;
    left: 34px; top: 124px;
    width: 532px;
    display: grid;
    grid-template-columns: repeat(3, 1fr);
    gap: 14px 16px;
    margin: 0; padding: 0;
    list-style: none;
  }
  .location { font-size: 11px; line-height: 1.4; color: var(--ink); white-space: nowrap; }
  .location__city { color: var(--green); font-weight: 700; font-size: 11.5px; text-transform: uppercase; letter-spacing: .3px; }
  .location__phone { color: var(--blue); font-weight: 700; }

  .stripes { position: absolute; left: 0; bottom: 28px; width: 600px; height: 16px; }
</style>
</head>
<body>
<div class="canvas">

  <section class="card card--front">
    <div class="brand">
      <span class="brand__square"></span>
      <span class="brand__name">Carl Brenton<br>Insurance Agency</span>
    </div>
    <div class="tagline">Serving Pine Street Since 1958</div>
    <div class="employee">EMPLOYEE NAME</div>

    <div class="band band--phones">
      <div class="band__row">
        <svg viewBox="0 0 14 14"><rect x="1" y="5" width="12" height="8" rx="1" fill="#fff"/><rect x="3" y="1" width="8" height="4" rx="1" fill="#fff"/></svg>
        0985-4417203
      </div>
      <div class="band__row">
        <svg viewBox="0 0 14 14"><path d="M3 1 L5 1 L6 4 L4.5 5.5 Q6 8.5 8.5 9.5 L10 8 L13 9 L13 11 Q12 13 10 13 Q2 11 1 3 Q1 1 3 1Z" fill="#fff"/></svg>
        0985-55012786
      </div>
    </div>

    <div class="band band--web">
      <div class="band__row">
        <svg viewBox="0 0 14 14"><rect x="1" y="3" width="12" height="8" fill="#fff"/><path d="M1 3 L7 8 L13 3" stroke="#6f8879" fill="none"/></svg>
        carl@brentonagency.com
      </div>
      <div class="band__row">
        <svg viewBox="0 0 14 14"><circle cx="7" cy="7" r="6" fill="none" stroke="#fff" stroke-width="1.4"/><path d="M1 7 H13 M7 1 V13" stroke="#fff"/></svg>
        www.carlbrenton.com
      </div>
    </div>
  </section>

  <section class="card card--back">
    <div class="brand">
      <span class="brand__square"></span>
      <span class="brand__name">Carl Brenton<br>Insurance Agency</span>
    </div>
    <div class="tagline">Serving Pine Street Since 1958</div>

    <ul class="locations">
      <li class="location">
        <div class="location__city">Home Office</div>
        <div>118 Pine Street, Oakridge</div>
        <div class="location__phone">0985-4417203</div>
      </li>
      <li class="location">
        <div class="location__city">Bayview</div>
        <div>42 Harbor Lane, Bayview</div>
        <div class="location__phone">0985-4417210</div>
      </li>
      <li class="location">
        <div class="location__city">Cedar Point</div>
        <div>905 Cedar Avenue, Cedar Point</div>
        <div class="location__phone">0985-4417225</div>
      </li>
      <li class="location">
        <div class="location__city">Millbrook</div>
        <div>27 Mill Road, Millbrook</div>
        <div class="location__phone">0985-4417238</div>
      </li>
      <li class="location">
        <div class="location__city">Riverbend</div>
        <div>310 River Drive, Riverbend</div>
        <div class="location__phone">0985-4417246</div>
      </li>
      <li class="location">
        <div class="location__city">Southfield</div>
        <div>64 Elm Court, Southfield</div>
        <div class="location__phone">0985-4417259</div>
      </li>
    </ul>

    <svg class="stripes" viewBox="0 0 600 16" aria-hidden="true">
      <path d="M0 4 H200 L212 12 H600" stroke="var(--slate)" stroke-width="3" fill="none"/>
      <path d="M0 10 H196 M216 6 H600" stroke="var(--blue)" stroke-width="3" fill="none"/>
    </svg>
  </section>

</div>
</body>
</html>
```